Lorvex Tilo medical cannibis cultivation company

tag - Tilo rise
Lorvex Tilo medical cannabis cultivation - logo is selected- can we please see bold examples with our selection. We are mainly dealing with medical companies and professionals. We would like to be stand out in the crowd with our designs. Welcome any and all attempts. Thanks

Target Market(s)

Medical and Professional

Industry/Entity Type

Medical And Science

Font styles to use
Sans Serif

Colors

Designer to choose colors to be used in the design.

Requirements
Must have
• Bright colour and be bold- Love the teal and magenta that is currently on the dark background design.
Nice to have
• shading and the 3D affect- The shadowed appearance.
Should not have
• Anything related to illegal activity or un professional manners

```html
<!DOCTYPE html>
<html lang="en">
<head>
<meta charset="utf-8">
<title>Lorvex Tilo – Stationery</title>
<link href="https://fonts.googleapis.com/css2?family=Questrial&family=Roboto:wght@400&display=swap" rel="stylesheet">
<style>
:root{
  --bg:#dcdcdc;
  --paper:#f6f6f6;
  --ink:#000;
  --teal:#1ba8e0;
  --magenta:#9b3d9e;
  --text:#4a4a4a;
  --ring:#8a8a8a;
  --shadow:0 1px 4px rgba(0,0,0,.18);
}
*{margin:0;padding:0;box-sizing:border-box}
html,body{width:1200px;height:877px;overflow:hidden;background:var(--bg)}
body{position:relative;font-family:"Questrial",sans-serif;color:var(--text)}
.sheet{position:absolute;background:var(--paper);box-shadow:var(--shadow)}

/* brand lockup */
.brand{display:flex;flex-direction:column;align-items:center;gap:3px}
.brand-dot{border:2px solid var(--ring);border-radius:50%}
.brand-name{font-family:"Questrial",sans-serif;color:var(--teal);text-transform:uppercase;white-space:nowrap;line-height:1}
.brand-tag{font-family:"Questrial",sans-serif;color:var(--teal);text-transform:uppercase;white-space:nowrap;line-height:1}

/* letterhead */
.letterhead{left:54px;top:65px;width:527px;height:743px}
.letterhead-band{height:98px;background:var(--ink);display:flex;justify-content:center;align-items:center}
.letterhead-band .brand-dot{width:40px;height:40px}
.letterhead-band .brand-name{font-size:17px}
.letterhead-band .brand-tag{font-size:7px;letter-spacing:1.5px}
.salutation{position:absolute;left:46px;top:209px;font-size:14px;color:#555}
.letter-body{position:absolute;left:46px;top:246px;width:438px;font-size:7.6px;line-height:11.4px;text-align:justify}
.letter-body p{margin-bottom:11.4px}
.closing{position:absolute;left:46px;top:487px;font-size:7.6px}
.signature{position:absolute;left:42px;top:521px;width:94px;height:38px;background:linear-gradient(90deg,rgba(30,70,160,.18),rgba(30,70,160,.06));border-radius:4px}
.letter-footer{position:absolute;left:0;right:0;top:690px;text-align:center;font-family:"Roboto",sans-serif;font-size:8px;line-height:11.2px;color:#555}
.letter-footer b{font-weight:400;color:var(--magenta)}

/* business cards */
.card{position:absolute;background:var(--ink);box-shadow:var(--shadow);display:flex;flex-direction:column;align-items:center;justify-content:center}
.card-front{left:617px;top:110px;width:247px;height:140px;color:#fff}
.card-front .brand-dot{width:26px;height:26px;margin-bottom:10px}
.card-person{font-size:8px;color:var(--teal)}
.card-person span{font-size:5px;color:var(--magenta)}
.card-details{font-family:"Roboto",sans-serif;font-size:4.8px;line-height:7.2px;text-align:center;margin-top:4px}
.card-back{left:880px;top:110px;width:249px;height:142px}
.card-back .brand-dot{width:58px;height:58px}
.card-back .brand-name{font-size:18px}
.card-back .brand-tag{font-size:7px;letter-spacing:1.5px}

/* envelopes */
.envelope-back{left:608px;top:299px;width:530px;height:241px}
.envelope-flap{position:absolute;left:0;top:0;width:530px;height:75px}
.envelope-flap .brand-dot{position:absolute;left:257px;top:26px;width:18px;height:18px}
.envelope-front{left:609px;top:568px;width:529px;height:240px}
.envelope-front .brand{position:absolute;left:28px;top:28px;width:100px}
.envelope-front .brand-dot{width:50px;height:50px}
.envelope-front .brand-name{font-size:14px}
.envelope-front .brand-tag{font-size:6px;letter-spacing:1.2px}
.envelope-address{position:absolute;left:17px;top:104px;width:132px;text-align:center;font-family:"Roboto",sans-serif;font-size:8px;line-height:10.6px;color:#555}
</style>
</head>
<body>

<section class="sheet letterhead">
  <header class="letterhead-band">
    <div class="brand">
      <div class="brand-dot"></div>
      <div class="brand-name">Lorvex Tilo</div>
      <div class="brand-tag">Tilo rise</div>
    </div>
  </header>
  <p class="salutation">Dear Mr. Voss,</p>
  <div class="letter-body">
    <p>Lorem ipsum dolor sit amet, consectetur adipiscing elit. Donec orci purus, luctus vitae dignissim eu, iaculis sed purus. Vivamus faucibus, ipsum nec aliquet viverra, leo mauris condimentum ligula, sit amet sagittis enim ligula quis arcu. Nam egestas tortor id nisi porttitor mattis. In tortor ante, ultricies in suscipit a, tempus non massa. Vivamus et auctor mi. Fusce vel massa nulla. Phasellus nec eros mauris, et scelerisque orci.</p>
    <p>Donec malesuada orci vitae nulla accumsan porta a id massa. Quisque accumsan iaculis magna sit amet fringilla. Maecenas consequat, magna eget tincidunt semper, odio nibh rutrum mi, id feugiat ante nisi eu risus. Vestibulum nunc orci, rhoncus a placerat in, ultricies in mi. Cras mattis varius eros, vel fringilla nisi suscipit eget. Quisque scelerisque sagittis nulla at porttitor.</p>
    <p>Sed id augue vitae urna euismod commodo aliquet a quam. Pellentesque arcu velit, cursus et malesuada ut, consequat et diam. Nullam erat sem, rhoncus id ullamcorper vitae, rhoncus et arcu. In ultricies ultricies nulla, ut rutrum nisi iaculis at. Donec eu magna a metus ornare faucibus. Fusce aliquet faucibus ultricies. Morbi semper, est id tincidunt gravida, sem arcu adipiscing lacus, ac bibendum nulla leo eu purus. Quisque nec diam sed risus consectetur a ccumsan quis quis nibh. Vestibulum id purus lorem.</p>
    <p>It is a long established fact that a reader will be distracted by the readable content of a page when looking at its layout. The point of using Lorem Ipsum is that it has a more-or-less normal distribution of letters, as opposed to using 'Content here, content here', making it look like readable English. Many desktop publishing packages</p>
  </div>
  <p class="closing">Sincerely,</p>
  <div class="signature" role="img" aria-label="Handwritten signature of Arlen Voss"></div>
  <footer class="letter-footer">
    4120 Larchmere Road, Halden Bay, Oregon 90412<br>
    <b>P:</b> 541 208 7316 <b>C:</b> 541 907 4482 <b>F:</b> 541 330 6025 <b>E:</b> arlen@lorvextilo.com<br>
    <b>W:</b> www.lorvextilo.com
  </footer>
</section>

<section class="card card-front">
  <div class="brand-dot"></div>
  <p class="card-person">Arlen Voss <span>- CEO/Founder</span></p>
  <p class="card-details">4120 Larchmere Road, Halden Bay, Oregon 90412<br>P: 541 208 7316 M: 541 907 4482 F: 541 330 6025<br>E: arlen@lorvextilo.com W: www.lorvextilo.com</p>
</section>

<section class="card card-back">
  <div class="brand">
    <div class="brand-dot"></div>
    <div class="brand-name">Lorvex Tilo</div>
    <div class="brand-tag">Tilo rise</div>
  </div>
</section>

<section class="sheet envelope-back">
  <svg class="envelope-flap" viewBox="0 0 530 75" width="530" height="75" aria-hidden="true">
    <path d="M0 0 H530 Q522 40 505 62 Q497 74 480 74 H50 Q33 74 25 62 Q8 40 0 0 Z" fill="#000"/>
  </svg>
  <div class="envelope-flap"><div class="brand-dot"></div></div>
</section>

<section class="sheet envelope-front">
  <div class="brand">
    <div class="brand-dot"></div>
    <div class="brand-name">Lorvex Tilo</div>
    <div class="brand-tag">Tilo rise</div>
  </div>
  <p class="envelope-address">4120 Larchmere Road<br>Halden Bay, Oregon 90412</p>
</section>

</body>
</html>
```